Roofing Company Modern look

I want a modern and sophisticated look for our roofing business.

Our address is :

5217 Mallow Creek Ln
Lakeview, Fl 32790

(407)-583-2196

www.HarborlineRoofsFl.com

I also want to make sure on the back there is a spot to put
Project Manager Name :

Number:

Because the cards will be used by all sales people

Project Manager Name :

Also there are accreditation we have logos are uploaded here as well that I would like maybe on the back of card as well

I also want to highlight our special attributions or trades:

Residential & Commercial
Fully Insured
License # CCC7482913
Insurance Claims
Serving Central Florida Since 1994
Free Estimates

Contact Information for Business Card

Our address is :

5217 Mallow Creek Ln
Lakeview, Fl 32790

(407)-583-2196

Project Manager Name :

Residential & Commercial
Fully Insured
License # CCC7482913
Insurance Claims
Free Estimates

Font styles to use
Serif
Sans Serif

Colors
3176b5

Requirements
Must have
• Must have royal blue like my logo grey and black are the colors I like

```html
<!DOCTYPE html>
<html lang="en">
<head>
<meta charset="utf-8">
<title>Harborline Roofing &amp; Gutters – Stationery</title>
<link rel="stylesheet" href="https://fonts.googleapis.com/css2?family=Open+Sans:wght@400;500;600&family=Arimo:wght@400;500&display=swap">
<style>
  :root {
    --royal: #0b57a8;
    --sky: #3176b5;
    --ink: #2e2e2e;
    --text: #555;
    --charcoal: #333;
    --paper: #ffffff;
    --backdrop: #e4e6e9;
  }
  * { box-sizing: border-box; margin: 0; padding: 0; }
  html, body { width: 1200px; height: 1200px; overflow: hidden; }
  body { background: var(--backdrop); position: relative; font-family: "Open Sans", sans-serif; }

  .letterhead {
    position: absolute; left: 50px; top: 215px; width: 600px; height: 771px;
    background: var(--paper); box-shadow: 0 2px 10px rgba(0,0,0,.18); overflow: hidden;
    border-bottom: 6px solid var(--charcoal);
  }
  .header-band { position: absolute; left: 0; top: 0; display: block; }

  .brand { position: absolute; display: flex; align-items: center; gap: 5px; color: var(--sky); font-family: "Arimo", sans-serif; font-weight: 500; }
  .brand-dot { border-radius: 50%; background: var(--sky); flex: none; }
  .brand-name { display: block; letter-spacing: 1px; line-height: 1; }
  .brand-sub { display: block; letter-spacing: .6px; line-height: 1.2; text-transform: uppercase; }

  .letterhead .brand { left: 62px; top: 96px; }
  .letterhead .brand-dot { width: 10px; height: 10px; }
  .letterhead .brand-name { font-size: 17px; }
  .letterhead .brand-sub { font-size: 5.5px; }

  .contact {
    position: absolute; left: 405px; top: 21px; padding-left: 10px;
    border-left: 1px solid rgba(255,255,255,.8);
    color: #fff; font-family: "Arimo", sans-serif; font-size: 9.5px; line-height: 11.5px; font-style: normal;
  }
  .contact p + p { margin-top: 7px; }
  .contact .row { display: flex; align-items: center; gap: 4px; }
  .contact svg { flex: none; }

  .letter { position: absolute; left: 56px; top: 139px; width: 486px; color: var(--text); font-size: 9.5px; line-height: 11.5px; }
  .letter .date { margin-bottom: 11px; }
  .letter .recipient { margin-bottom: 33px; }
  .letter .salutation { margin-bottom: 23px; }
  .letter .body p { line-height: 17.2px; text-align: justify; margin-bottom: 17px; }
  .letter .closing { margin-top: 25px; }
  .signature { display: block; width: 140px; height: 18px; margin-top: 9px; border-radius: 2px; background: linear-gradient(90deg, #e7e7e7, #f3f3f3); }
  .signer { margin-top: 9px; font-size: 12px; font-weight: 500; color: var(--ink); }
  .signer-role { margin-top: 4px; }

  .footer { position: absolute; left: 56px; right: 42px; top: 714px; display: flex; justify-content: space-between; align-items: flex-end; }
  .credentials { display: grid; grid-template-columns: auto auto; column-gap: 6px; font-family: "Arimo", sans-serif; font-size: 9.5px; line-height: 11.5px; color: var(--ink); }
  .credentials li { list-style: none; display: flex; align-items: center; gap: 4px; white-space: nowrap; }
  .credentials li::before { content: ""; width: 6px; height: 6px; border-radius: 50%; background: var(--sky); }
  .credentials li.plain::before { display: none; }
  .badges { display: flex; gap: 12px; align-items: center; }

  .envelope { position: absolute; left: 692px; width: 466px; height: 233px; background: var(--paper); box-shadow: 0 2px 10px rgba(0,0,0,.18); overflow: hidden; }
  .envelope.front { top: 385px; }
  .envelope.back { top: 657px; border-bottom: 5px solid var(--charcoal); }
  .envelope .brand { left: 41px; top: 74px; }
  .envelope .brand-dot { width: 8px; height: 8px; }
  .envelope .brand-name { font-size: 13px; }
  .envelope .brand-sub { font-size: 4.5px; }
  .envelope .return-address { position: absolute; right: 36px; top: 31px; color: #fff; font-family: "Arimo", sans-serif; font-size: 7.5px; }
  .flap { position: absolute; left: 0; top: 0; display: block; }
</style>
</head>
<body>

<section class="letterhead">
  <svg class="header-band" width="600" height="130" viewBox="0 0 600 130" aria-hidden="true">
    <path fill="var(--royal)" d="M0,0 H600 V104 C470,122 330,60 0,82 Z"/>
    <path fill="none" stroke="var(--charcoal)" stroke-width="3" d="M0,90 C330,68 470,130 600,112"/>
  </svg>

  <div class="brand">
    <span class="brand-dot"></span>
    <span><span class="brand-name">HARBORLINE</span><span class="brand-sub">Roofing &amp; Gutters Inc.</span></span>
  </div>

  <address class="contact">
    <p>5217 Mallow Creek Ln<br>Lakeview, Fl 32790</p>
    <p>
      <span class="row"><svg width="8" height="8" viewBox="0 0 10 10"><path fill="none" stroke="#fff" stroke-width="1.2" d="M2,1 L4,3 L3,4.5 C4,6 4.5,6.5 5.5,7 L7,6 L9,8 L8,9 C4,9 1,6 1,2 Z"/></svg>(407)-583-2196</span>
      <span class="row"><svg width="8" height="8" viewBox="0 0 10 10"><circle cx="5" cy="5" r="4" fill="none" stroke="#fff"/><path d="M1,5 H9 M5,1 C2.5,4 2.5,6 5,9 C7.5,6 7.5,4 5,1" fill="none" stroke="#fff" stroke-width=".8"/></svg>www.HarborlineRoofsFl.com</span>
    </p>
  </address>

  <article class="letter">
    <p class="date">Issuing Date: May 5, 2018</p>
    <p class="recipient">Name Of Employee Mr. XYZABC<br>Address of Employee<br>Address Line 2 etc..</p>
    <p class="salutation">Dear Mr.XYZABC</p>
    <div class="body">
      <p>Lorem Ipsum has been the industry's standard dummy text ever since the 1500s, when an unknown printer took a galley of type and scrambled it to make a type specimen book. It has survived not only five centuries, but also the leap into electronic typesetting, remaining essentially unchanged. It was popularised in the 1960s with the release of transfer sheets containing Lorem Ipsum passages, and more recently with desktop layout software including versions of Lorem Ipsum.</p>
      <p>Lorem Ipsum is simply dummy text of the printing and typesetting industry. Lorem Ipsum has been the industry's standard dummy text ever since the 1500s, when an unknown printer took a galley of type and scrambled it to make a type specimen book.</p>
      <p>It has survived not only five centuries, but also the leap into electronic typesetting, remaining essentially unchanged. It was popularised in the 1960s with the release of transfer sheets containing Lorem Ipsum passages.</p>
    </div>
    <p class="closing">Yours Sincerely</p>
    <span class="signature" role="img" aria-label="Handwritten signature of Marcus Ellery"></span>
    <p class="signer">Marcus Ellery</p>
    <p class="signer-role">Managing Director</p>
  </article>

  <footer class="footer">
    <ul class="credentials">
      <li>Residential &amp; Commercial</li><li>Fully Insured</li>
      <li>License # CCC7482913</li><li>Insurance Claims</li>
      <li>Serving Central Florida Since 1994</li><li class="plain">Free Estimates</li>
    </ul>
    <div class="badges" aria-label="Accreditation badges">
      <svg width="64" height="18" viewBox="0 0 64 18" aria-hidden="true"><rect x=".5" y=".5" width="63" height="17" fill="#c8102e" stroke="#555"/></svg>
      <svg width="20" height="34" viewBox="0 0 20 34" aria-hidden="true"><rect width="20" height="34" rx="2" fill="var(--royal)"/></svg>
      <svg width="36" height="36" viewBox="0 0 36 36" aria-hidden="true"><circle cx="18" cy="18" r="16" fill="#fff" stroke="#3b4a5c" stroke-width="3"/></svg>
      <svg width="44" height="34" viewBox="0 0 44 34" aria-hidden="true"><polygon points="11,0 33,0 44,17 33,34 11,34 0,17" fill="#1e2c4f"/></svg>
    </div>
  </footer>
</section>

<section class="envelope front">
  <svg class="header-band" width="466" height="101" viewBox="0 0 600 130" aria-hidden="true">
    <path fill="var(--royal)" d="M0,0 H600 V104 C470,122 330,60 0,82 Z"/>
    <path fill="none" stroke="var(--charcoal)" stroke-width="3" d="M0,90 C330,68 470,130 600,112"/>
  </svg>
  <div class="brand">
    <span class="brand-dot"></span>
    <span><span class="brand-name">HARBORLINE</span><span class="brand-sub">Roofing &amp; Gutters Inc.</span></span>
  </div>
  <p class="return-address">5217 Mallow Creek Ln Lakeview, Fl 32790</p>
</section>

<section class="envelope back">
  <svg class="flap" width="466" height="56" viewBox="0 0 466 56" aria-hidden="true">
    <polygon points="0,0 466,0 448,56 18,56" fill="var(--royal)"/>
  </svg>
</section>

</body>
</html>
```